web page look and feel - B2B enterprise application

We have an enterprise application with 10 to 15 core pages and several supporting pages or popups. To start, we want the graphical design of the Users, Roles and Data Source pages and their supporting popups, wizards, etc. to be made beautiful. That is around 10 pages in total. There is a fair amount of redundancy among the pages. I have attached 5 screenshots. We very much want the pages to project a premium feel. That is absolutely essential. The color scheme is blue and sometimes yellow (only if it makes the page look better) plus black, gray and white. If the design of these screens goes well, we would expand the project to continue with other pages. The core of what we are looking for is graphic in nature but we are open to workflow suggestions if you have them. The Roles screen needs some improvements to the layout. I am looking for everything that includes icons, fonts, spacing, etc. I assume getting to the final design will take some back and forth with multiple revisions.

Target Market(s)

Large Enterprises

Number of Pages Required

5+ page

Requirements
Must have
• Premium feel

```html
<!DOCTYPE html>
<html lang="en">
<head>
<meta charset="utf-8">
<title>Users – Northwind Data</title>
<link rel="stylesheet" href="https://fonts.googleapis.com/css2?family=Catamaran:wght@400;500;600;700&family=Montserrat:wght@400;500&display=swap">
<style>
:root{
  --navy:#173a55;
  --navy-hi:#25506f;
  --accent:#0fa3d6;
  --teal-a:#27b6c3;
  --teal-b:#1c9dd3;
  --ink:#3c4550;
  --muted:#7e8790;
  --line:#cfd5da;
  --row-alt:#f3f4f5;
  --ok:#13c98e;
  --white:#ffffff;
}
*{box-sizing:border-box;margin:0;padding:0}
html,body{width:1200px;height:786px;overflow:hidden;background:var(--white)}
body{font-family:"Catamaran",sans-serif;color:var(--ink);position:relative}
svg{display:block}

/* sidebar */
.sidebar{position:absolute;left:0;top:0;width:300px;height:786px;background:var(--navy);color:var(--white)}
.brand{height:80px;background:linear-gradient(90deg,var(--teal-a),var(--teal-b));display:flex;align-items:center;gap:10px;padding-left:48px}
.brand-dot{width:22px;height:22px;border-radius:50%;background:var(--white)}
.brand-name{font-size:26px;font-weight:600;color:var(--white);letter-spacing:-.3px}
.profile{position:absolute;top:100px;left:40px;display:flex;gap:10px;align-items:center}
.avatar{width:40px;height:40px;border-radius:50%;background:radial-gradient(circle at 50% 40%,#c9a58c,#4a3a35);border:2px solid #e7e7e7}
.profile-name{font-family:"Montserrat",sans-serif;font-size:15px;font-weight:500;line-height:18px}
.profile-mail{font-family:"Montserrat",sans-serif;font-size:12px;color:#b6c2cc;line-height:18px}
.divider{position:absolute;top:160px;left:20px;width:260px;height:1px;background:#3f5e77}
.nav{position:absolute;top:176px;left:20px;width:280px;list-style:none}
.nav li{height:32px;display:flex;align-items:center;font-size:15px;position:relative}
.nav .group{background:var(--navy-hi);height:33px;margin-bottom:-1px}
.nav .group::after{content:"";position:absolute;right:0;top:0;width:5px;height:100%;background:var(--accent)}
.nav .icon{width:52px;display:flex;justify-content:center}
.nav .sub{padding-left:42px}
.nav .sub .icon{width:28px;justify-content:flex-start}
.nav .chev{position:absolute;right:36px;top:11px}
.clock-row{position:absolute;top:658px;left:30px;right:30px;display:flex;justify-content:space-between;font-size:15px;font-weight:600}
.clock-row span{display:flex;align-items:center;gap:10px}

/* top bar */
.topbar{position:absolute;left:300px;top:0;width:900px;height:80px;border-bottom:1px solid #e6e9ec}
.topbar .menu{position:absolute;left:30px;top:31px}
.tools{position:absolute;left:492px;top:28px;display:flex;gap:24px}
.user-menu{position:absolute;right:30px;top:28px;display:flex;align-items:center;gap:10px;font-size:17px;font-weight:500;color:#5a636c}

/* page head */
.page-title{position:absolute;left:357px;top:112px;font-family:"Montserrat",sans-serif;font-size:31px;font-weight:400;color:#3b4148}
.btn-add{position:absolute;left:462px;top:122px;width:60px;height:26px;background:var(--accent);color:var(--white);border:none;font:700 15px "Catamaran",sans-serif;box-shadow:0 0 8px rgba(15,163,214,.55)}
.search{position:absolute;right:30px;top:122px;display:flex;gap:14px;align-items:center;font-size:16px;color:#8c949b}

/* tables */
.grid{position:absolute;left:330px;width:840px;border:1px solid var(--line);border-bottom:none}
.row{display:grid;grid-template-columns:40px 137px 137px 137px 137px 137px 1fr;height:39px;border-bottom:1px solid var(--line);font-size:16px}
.row>div{display:flex;align-items:center;justify-content:center;border-right:1px solid var(--line)}
.row>div:last-child{border-right:none}
.row.head{font-weight:500;font-size:16px;color:#3b4148}
.actions{gap:10px}
.act{width:20px;height:20px;background:var(--accent);border-radius:2px;display:flex;align-items:center;justify-content:center}
.perm{display:grid;grid-template-columns:419px 1fr;height:39px;border-bottom:1px solid var(--line);font-size:16px}
.perm>div{display:flex;align-items:center;justify-content:center;gap:6px}
.perm>div:first-child{border-right:1px solid var(--line)}
.perm.head{background:var(--accent);color:var(--white);font-weight:600}
.perm.head>div:first-child{border-color:#ffffff55}
.perm.alt{background:var(--row-alt)}
.ok{margin-left:14px}
.ok:first-child{margin-left:0}
.perm-edit{height:39px;border-bottom:1px solid var(--line);display:flex;align-items:center;justify-content:center;color:var(--accent);font-weight:600;font-size:16px}

/* pager */
.pager{position:absolute;left:677px;top:736px;display:flex;align-items:center;gap:6px;font-size:15px;color:#b0b6bb}
.pager .current{color:#4b535b}
.per-page{margin-left:18px;background:#9a9fa4;color:var(--white);font-size:13px;font-weight:700;padding:0 5px;height:17px;display:flex;align-items:center;gap:2px}
</style>
</head>
<body>

<aside class="sidebar">
  <div class="brand"><span class="brand-dot"></span><span class="brand-name">Northwind Data</span></div>
  <div class="profile">
    <div class="avatar" role="img" aria-label="Profile photo of the signed-in user"></div>
    <div><div class="profile-name">Dana Reyes</div><div class="profile-mail">dana.reyes@example.com</div></div>
  </div>
  <div class="divider"></div>
  <ul class="nav">
    <li class="group"><span class="icon"><svg width="16" height="16" viewBox="0 0 16 16"><circle cx="8" cy="4.5" r="3.5" fill="#2fa7e0"/><path d="M1.5 16c0-4 3-6.5 6.5-6.5s6.5 2.5 6.5 6.5z" fill="#2fa7e0"/></svg></span>User
      <svg class="chev" width="10" height="6" viewBox="0 0 10 6"><path d="M1 1l4 4 4-4" stroke="#c6d2db" fill="none" stroke-width="1.4"/></svg></li>
    <li class="sub"><span class="icon"><svg width="16" height="16" viewBox="0 0 16 16" fill="none" stroke="#fff" stroke-width="1.2"><circle cx="8" cy="4.5" r="3.3"/><path d="M1.8 15.5c0-3.7 2.8-6 6.2-6s6.2 2.3 6.2 6z"/></svg></span>Roles</li>
    <li class="sub"><span class="icon"><svg width="16" height="17" viewBox="0 0 16 17" fill="none" stroke="#fff" stroke-width="1.2"><path d="M3 12V7.5a5 5 0 0110 0V12l1.5 1.5h-13z"/><path d="M6.5 15a1.6 1.6 0 003 0"/></svg></span>Notification Groups</li>
    <li class="group"><span class="icon"><svg width="18" height="14" viewBox="0 0 18 14"><rect width="18" height="4" rx="1" fill="#2fa7e0"/><rect y="5" width="18" height="4" rx="1" fill="#2fa7e0"/><rect y="10" width="18" height="4" rx="1" fill="#2fa7e0"/></svg></span>Data Source
      <svg class="chev" width="10" height="6" viewBox="0 0 10 6"><path d="M1 1l4 4 4-4" stroke="#c6d2db" fill="none" stroke-width="1.4"/></svg></li>
    <li class="sub"><span class="icon"><svg width="18" height="16" viewBox="0 0 18 16" fill="none" stroke="#fff" stroke-width="1.3"><path d="M7 1h9v14H7M1 8h10M8 5l3 3-3 3"/></svg></span>Data Object Relationship</li>
    <li><span class="icon"><svg width="18" height="18" viewBox="0 0 18 18" fill="#fff"><rect width="8" height="18"/><rect x="10" width="8" height="8"/><rect x="10" y="10" width="8" height="8"/></svg></span>Data Sets</li>
    <li><span class="icon"><svg width="18" height="18" viewBox="0 0 18 18" fill="#fff"><rect width="7" height="18"/><rect x="9" width="9" height="3"/><rect x="9" y="5" width="9" height="3"/><rect x="9" y="10" width="9" height="3"/><rect x="9" y="15" width="9" height="3"/></svg></span>Rule Sets</li>
    <li><span class="icon"><svg width="18" height="18" viewBox="0 0 18 18" fill="none" stroke="#fff" stroke-width="1.6"><circle cx="9" cy="9" r="8"/><path d="M9 4v5l3 2"/></svg></span>Schedule</li>
    <li class="group"><span class="icon"><svg width="18" height="16" viewBox="0 0 18 16" fill="none" stroke="#2fa7e0" stroke-width="1.6"><path d="M15 6A6.5 6.5 0 003 5M3 10a6.5 6.5 0 0012 1"/><path d="M1 3l2 2.5L5.5 3.5M17 13l-2-2.5-2.5 2"/></svg></span>Metadata Import/Export
      <svg class="chev" width="10" height="6" viewBox="0 0 10 6"><path d="M1 1l4 4 4-4" stroke="#c6d2db" fill="none" stroke-width="1.4"/></svg></li>
    <li class="sub"><span class="icon"><svg width="12" height="16" viewBox="0 0 12 16" fill="none" stroke="#fff" stroke-width="1.4"><path d="M6 1v14M1 10l5 5 5-5"/></svg></span>Import</li>
    <li class="sub"><span class="icon"><svg width="12" height="16" viewBox="0 0 12 16" fill="none" stroke="#fff" stroke-width="1.4"><path d="M6 15V1M1 6l5-5 5 5"/></svg></span>Export</li>
  </ul>
  <div class="clock-row">
    <span><svg width="24" height="26" viewBox="0 0 24 26" fill="none" stroke="#fff" stroke-width="2"><rect x="1" y="4" width="22" height="21" rx="2"/><path d="M1 9h22M6 1v5M18 1v5"/><text x="12" y="22" font-size="11" font-weight="700" fill="#fff" stroke="none" text-anchor="middle" font-family="Catamaran,sans-serif">5</text></svg>July 05</span>
    <span><svg width="24" height="24" viewBox="0 0 24 24" fill="none" stroke="#fff" stroke-width="2"><circle cx="12" cy="12" r="11"/><path d="M12 5v7h-4"/></svg>18:36</span>
  </div>
</aside>

<header class="topbar">
  <svg class="menu" width="18" height="16" viewBox="0 0 18 16" fill="#6b737a"><rect width="18" height="2.5"/><rect y="6.5" width="18" height="2.5"/><rect y="13" width="18" height="2.5"/></svg>
  <div class="tools">
    <svg width="26" height="24" viewBox="0 0 26 24" fill="none" stroke="#6b737a" stroke-width="2.2"><path d="M2 18a11 11 0 0122 0"/><path d="M13 18l5-7"/></svg>
    <svg width="26" height="24" viewBox="0 0 26 24" fill="none" stroke="#6b737a" stroke-width="2"><path d="M2 22L17 7"/><path d="M20 1v3M23 4h-3M21 9h2M16 2v2" stroke-width="1.4"/></svg>
    <svg width="26" height="24" viewBox="0 0 26 24"><circle cx="12" cy="12" r="11.5" fill="#1a9fd4"/><text x="12" y="17.5" text-anchor="middle" font-size="17" font-weight="700" fill="#fff" font-family="Catamaran,sans-serif">?</text></svg>
    <svg width="26" height="24" viewBox="0 0 26 24" fill="#6b737a"><circle cx="9" cy="9" r="6.5"/><circle cx="9" cy="9" r="2.4" fill="#fff"/><circle cx="19" cy="18" r="5"/><circle cx="19" cy="18" r="1.8" fill="#fff"/></svg>
  </div>
  <div class="user-menu">
    <svg width="20" height="24" viewBox="0 0 20 24" fill="#6b737a"><circle cx="10" cy="6" r="5.5"/><path d="M0 24c0-7 4-11 10-11s10 4 10 11z"/></svg>
    Dana Reyes
    <svg width="12" height="8" viewBox="0 0 12 8"><path d="M1 1l5 5 5-5" stroke="#6b737a" fill="none" stroke-width="1.4"/></svg>
  </div>
</header>

<main>
  <h1 class="page-title">Users</h1>
  <button class="btn-add">Add</button>
  <div class="search"><svg width="22" height="22" viewBox="0 0 22 22" fill="none" stroke="#9aa1a7" stroke-width="1.5"><circle cx="9" cy="9" r="8"/><path d="M15 15l6 6"/></svg>Search</div>

  <section class="grid" style="top:188px">
    <div class="row head"><div></div><div>First Name</div><div>Last Name</div><div>Username</div><div>Email</div><div>Status</div><div>Edit</div></div>
    <div class="row">
      <div><svg width="7" height="10" viewBox="0 0 7 10"><path d="M1 1l4 4-4 4" stroke="#9aa1a7" fill="none" stroke-width="1.4"/></svg></div>
      <div>Test</div><div>Test</div><div>test.1</div><div>test@example.com</div><div>Active</div>
      <div class="actions">
        <span class="act"><svg width="12" height="12" viewBox="0 0 12 12" fill="none" stroke="#fff" stroke-width="1.3"><path d="M2 10l1-3 6-6 2 2-6 6zM1 11.5h10"/></svg></span>
        <span class="act"><svg width="12" height="12" viewBox="0 0 12 12" fill="none" stroke="#fff" stroke-width="1.3"><rect x="4" y="4" width="7" height="7"/><path d="M8 2V1H1v7h1"/></svg></span>
        <span class="act"><svg width="12" height="12" viewBox="0 0 12 12" fill="none" stroke="#fff" stroke-width="1.3"><path d="M1 3h10M4 3V1h4v2M2.5 3l.8 8.5h5.4L9.5 3M5 5v5M7 5v5"/></svg></span>
      </div>
    </div>
    <div class="perm head"><div>Object</div><div>Permissions</div></div>
    <div class="perm"><div>System Settings</div><div>
      <svg class="ok" width="20" height="20" viewBox="0 0 20 20"><circle cx="10" cy="10" r="10" fill="#13c98e"/><path d="M5 10l3.5 3.5L15 7" stroke="#fff" stroke-width="2.4" fill="none"/></svg>Read
      <svg class="ok" width="20" height="20" viewBox="0 0 20 20"><circle cx="10" cy="10" r="10" fill="#13c98e"/><path d="M5 10l3.5 3.5L15 7" stroke="#fff" stroke-width="2.4" fill="none"/></svg>Write</div></div>
    <div class="perm"><div>Users</div><div>
      <svg class="ok" width="20" height="20" viewBox="0 0 20 20"><circle cx="10" cy="10" r="10" fill="#13c98e"/><path d="M5 10l3.5 3.5L15 7" stroke="#fff" stroke-width="2.4" fill="none"/></svg>Read
      <svg class="ok" width="20" height="20" viewBox="0 0 20 20"><circle cx="10" cy="10" r="10" fill="#13c98e"/><path d="M5 10l3.5 3.5L15 7" stroke="#fff" stroke-width="2.4" fill="none"/></svg>Write</div></div>
    <div class="perm alt"><div>Data Source</div><div>Role</div></div>
    <div class="perm"><div>All Data Sources</div><div>All Administrator</div></div>
    <div class="perm-edit">Edit</div>
  </section>

  <section class="grid" style="top:511px">
    <div class="row"><div><svg width="10" height="7" viewBox="0 0 10 7"><path d="M1 1l4 4 4-4" stroke="#9aa1a7" fill="none" stroke-width="1.4"/></svg></div><div>Test</div><div>Test</div><div>test.1</div><div>test@example.com</div><div>Active</div>
      <div class="actions"><span class="act"><svg width="12" height="12" viewBox="0 0 12 12" fill="none" stroke="#fff" stroke-width="1.3"><path d="M2 10l1-3 6-6 2 2-6 6zM1 11.5h10"/></svg></span><span class="act"><svg width="12" height="12" viewBox="0 0 12 12" fill="none" stroke="#fff" stroke-width="1.3"><rect x="4" y="4" width="7" height="7"/><path d="M8 2V1H1v7h1"/></svg></span><span class="act"><svg width="12" height="12" viewBox="0 0 12 12" fill="none" stroke="#fff" stroke-width="1.3"><path d="M1 3h10M4 3V1h4v2M2.5 3l.8 8.5h5.4L9.5 3M5 5v5M7 5v5"/></svg></span></div></div>
    <div class="row"><div><svg width="10" height="7" viewBox="0 0 10 7"><path d="M1 1l4 4 4-4" stroke="#9aa1a7" fill="none" stroke-width="1.4"/></svg></div><div>Test</div><div>Test</div><div>test.1</div><div>test@example.com</div><div>Active</div>
      <div class="actions"><span class="act"><svg width="12" height="12" viewBox="0 0 12 12" fill="none" stroke="#fff" stroke-width="1.3"><path d="M2 10l1-3 6-6 2 2-6 6zM1 11.5h10"/></svg></span><span class="act"><svg width="12" height="12" viewBox="0 0 12 12" fill="none" stroke="#fff" stroke-width="1.3"><rect x="4" y="4" width="7" height="7"/><path d="M8 2V1H1v7h1"/></svg></span><span class="act"><svg width="12" height="12" viewBox="0 0 12 12" fill="none" stroke="#fff" stroke-width="1.3"><path d="M1 3h10M4 3V1h4v2M2.5 3l.8 8.5h5.4L9.5 3M5 5v5M7 5v5"/></svg></span></div></div>
    <div class="row"><div><svg width="10" height="7" viewBox="0 0 10 7"><path d="M1 1l4 4 4-4" stroke="#9aa1a7" fill="none" stroke-width="1.4"/></svg></div><div>Test</div><div>Test</div><div>test.1</div><div>test@example.com</div><div>Active</div>
      <div class="actions"><span class="act"><svg width="12" height="12" viewBox="0 0 12 12" fill="none" stroke="#fff" stroke-width="1.3"><path d="M2 10l1-3 6-6 2 2-6 6zM1 11.5h10"/></svg></span><span class="act"><svg width="12" height="12" viewBox="0 0 12 12" fill="none" stroke="#fff" stroke-width="1.3"><rect x="4" y="4" width="7" height="7"/><path d="M8 2V1H1v7h1"/></svg></span><span class="act"><svg width="12" height="12" viewBox="0 0 12 12" fill="none" stroke="#fff" stroke-width="1.3"><path d="M1 3h10M4 3V1h4v2M2.5 3l.8 8.5h5.4L9.5 3M5 5v5M7 5v5"/></svg></span></div></div>
    <div class="row"><div><svg width="10" height="7" viewBox="0 0 10 7"><path d="M1 1l4 4 4-4" stroke="#9aa1a7" fill="none" stroke-width="1.4"/></svg></div><div>Test</div><div>Test</div><div>test.1</div><div>test@example.com</div><div>Active</div>
      <div class="actions"><span class="act"><svg width="12" height="12" viewBox="0 0 12 12" fill="none" stroke="#fff" stroke-width="1.3"><path d="M2 10l1-3 6-6 2 2-6 6zM1 11.5h10"/></svg></span><span class="act"><svg width="12" height="12" viewBox="0 0 12 12" fill="none" stroke="#fff" stroke-width="1.3"><rect x="4" y="4" width="7" height="7"/><path d="M8 2V1H1v7h1"/></svg></span><span class="act"><svg width="12" height="12" viewBox="0 0 12 12" fill="none" stroke="#fff" stroke-width="1.3"><path d="M1 3h10M4 3V1h4v2M2.5 3l.8 8.5h5.4L9.5 3M5 5v5M7 5v5"/></svg></span></div></div>
    <div class="row"><div><svg width="10" height="7" viewBox="0 0 10 7"><path d="M1 1l4 4 4-4" stroke="#9aa1a7" fill="none" stroke-width="1.4"/></svg></div><div>Test</div><div>Test</div><div>test.1</div><div>test@example.com</div><div>Active</div>
      <div class="actions"><span class="act"><svg width="12" height="12" viewBox="0 0 12 12" fill="none" stroke="#fff" stroke-width="1.3"><path d="M2 10l1-3 6-6 2 2-6 6zM1 11.5h10"/></svg></span><span class="act"><svg width="12" height="12" viewBox="0 0 12 12" fill="none" stroke="#fff" stroke-width="1.3"><rect x="4" y="4" width="7" height="7"/><path d="M8 2V1H1v7h1"/></svg></span><span class="act"><svg width="12" height="12" viewBox="0 0 12 12" fill="none" stroke="#fff" stroke-width="1.3"><path d="M1 3h10M4 3V1h4v2M2.5 3l.8 8.5h5.4L9.5 3M5 5v5M7 5v5"/></svg></span></div></div>
  </section>

  <nav class="pager">
    <svg width="7" height="11" viewBox="0 0 7 11"><path d="M6 1L1.5 5.5 6 10" stroke="#4b535b" fill="none" stroke-width="1.6"/></svg>
    <span class="current">1</span><span>2</span><span>3</span><span>4</span>
    <svg width="7" height="11" viewBox="0 0 7 11"><path d="M1 1l4.5 4.5L1 10" stroke="#4b535b" fill="none" stroke-width="1.6"/></svg>
    <span class="per-page">20<svg width="7" height="5" viewBox="0 0 7 5"><path d="M1 1l2.5 2.5L6 1" stroke="#fff" fill="none" stroke-width="1.3"/></svg></span>
  </nav>
</main>

</body>
</html>
```